continued... Web Design for Professional Development and marketplace

in addition to the homepages that you are desiging, can you also create designs for the attached wireframes that are part of the same website.
I am creating this as a seperate project as we are keen to see your designs for the rest of the website.
VIdeo of prototype and homepage designs
https://www.quillvane.com/sh/rk7tpa2mw9qhb3c/8Lw2oNv4Zy/design
Updates
added an additional wireframe that was missed in the original upload
added one more wireframe for the homepage: where the user is prompted to login or signup
Industry/Entity Type
Marketplace
Look and feel
Each slider illustrates characteristics of the customer's brand and the style your logo design should communicate.

```html
<!DOCTYPE html>
<html lang="en">
<head>
<meta charset="utf-8">
<title>Competency Planning Tool – Halden School of Business</title>
<link href="https://fonts.googleapis.com/css2?family=Open+Sans:wght@400;600;700&family=Ubuntu:wght@400;500;700&display=swap" rel="stylesheet">
<style>
:root{
  --ink:#2b2f38;
  --ink-soft:#4a505b;
  --orange:#f39c12;
  --orange-deep:#e8860b;
  --band:#e2e2e2;
  --text:#333;
  --muted:#777;
  --line:#d4d4d4;
  --white:#fff;
}
*{box-sizing:border-box;margin:0;padding:0}
html,body{width:1109px;height:1200px;overflow:hidden;background:var(--white);font-family:"Open Sans",sans-serif;color:var(--text)}
.wrap{width:903px;margin-left:97px;position:relative}

/* header */
.topbar{height:74px;background:var(--ink)}
.topbar .wrap{height:74px}
.menu-btn{position:absolute;left:1px;top:14px;width:54px;height:43px;background:var(--ink-soft);display:flex;flex-direction:column;justify-content:center;align-items:center;gap:6px}
.menu-btn span{display:block;width:32px;height:3px;background:var(--white)}
.search{position:absolute;left:57px;top:14px;width:149px;height:43px;background:var(--white);font-size:16px;color:#999;padding:11px 12px;font-weight:300}
.search-btn{position:absolute;left:207px;top:14px;width:45px;height:43px;background:var(--ink-soft);display:flex;align-items:center;justify-content:center}
.brand{position:absolute;left:353px;top:10px;width:200px;text-align:center;color:var(--white);font-family:"Ubuntu",sans-serif;font-weight:400;line-height:1}
.brand .l1{font-size:29px;display:block}
.brand .l2{font-size:18px;display:block;margin-top:4px}
.signup{position:absolute;left:586px;top:29px;font-size:13px;color:var(--white);font-weight:600}
.signup em{font-style:normal;color:#888;font-weight:400;margin-left:4px}
.login{position:absolute;left:660px;top:14px;width:96px;height:43px;background:var(--ink-soft);color:var(--white);font-size:15px;display:flex;align-items:center;justify-content:center;gap:8px}
.add-review{position:absolute;left:759px;top:14px;width:143px;height:43px;background:var(--orange);color:var(--white);font-size:15px;display:flex;align-items:center;justify-content:center;gap:8px}

.navbar{height:30px;background:var(--orange)}
.navbar ul{list-style:none;display:flex;justify-content:flex-end;gap:26px;height:30px;align-items:center;font-size:13px;color:var(--white)}

/* filters */
.filters{margin-top:6px;height:65px;border:1px solid var(--line);display:flex;box-shadow:0 1px 2px rgba(0,0,0,.08)}
.filter{border-left:1px solid var(--line);text-align:center;font-size:14px;color:#555;padding-top:7px;line-height:1.3}
.filter:first-of-type{border-left:0}
.filter small{display:block;font-size:12px;color:var(--orange)}
.filter svg{display:block;margin:0 auto 2px}
.filter.save{background:var(--orange);color:var(--white);font-weight:700;width:93px;padding-top:14px}

/* intro */
.page-title{font-family:"Ubuntu",sans-serif;font-weight:700;color:var(--orange-deep);font-size:29px;margin-top:33px;line-height:1}
.lead{font-size:15px;color:#444;margin-top:7px;padding-bottom:11px;border-bottom:1px solid var(--line)}
.section-title{font-size:20px;font-weight:600;color:var(--text);margin-top:40px;height:37px}

/* groups */
.group{height:246px}
.group.shade{background:var(--band)}
.group .wrap{padding-top:16px}
.grid{display:grid;grid-template-columns:420px 154px 184px 180px;align-items:center}
.grid .head-q{font-size:15px;font-weight:600;color:var(--text);height:20px}
.grid .head-lvl{font-size:15px;color:#555;text-align:center;font-weight:600;opacity:.85}
.row{height:56px}
.row.tall{height:61px}
.q{font-size:13px;color:var(--muted);line-height:1.35}
.radio{justify-self:center;width:15px;height:15px;border-radius:50%;background:var(--white);border:1px solid #c4c4c4;position:relative}
.radio.on::after{content:"";position:absolute;left:3px;top:3px;width:7px;height:7px;border-radius:50%;background:var(--orange)}
.col-adv{transform:translateX(50px)}
.col-mod{transform:translateX(57px)}
.col-beg{transform:translateX(32px)}

.next-btn{position:absolute;left:97px;top:1123px;width:241px;height:43px;background:var(--orange);color:var(--white);font-size:15px;font-weight:600;display:flex;align-items:center;justify-content:center;gap:10px}
</style>
</head>
<body>
<header class="topbar">
  <div class="wrap">
    <div class="menu-btn"><span></span><span></span><span></span></div>
    <div class="search">Search</div>
    <div class="search-btn"><svg width="20" height="20" viewBox="0 0 20 20"><circle cx="8" cy="8" r="6" fill="none" stroke="#fff" stroke-width="2.6"/><line x1="12.5" y1="12.5" x2="18" y2="18" stroke="#fff" stroke-width="3" stroke-linecap="round"/></svg></div>
    <div class="brand"><span class="l1">Halden School</span><span class="l2">of Business</span></div>
    <div class="signup">Sign Up<em>or</em></div>
    <div class="login"><svg width="20" height="22" viewBox="0 0 20 22"><circle cx="10" cy="6" r="5" fill="#fff"/><path d="M1 21c0-6 4-9 9-9s9 3 9 9z" fill="#fff"/></svg>Login</div>
    <div class="add-review"><svg width="26" height="20" viewBox="0 0 26 20"><rect x="1" y="2" width="20" height="13" fill="none" stroke="#fff" stroke-width="1.6"/><line x1="5" y1="6" x2="17" y2="6" stroke="#fff"/><line x1="5" y1="9" x2="17" y2="9" stroke="#fff"/><path d="M5 15l-2 4 6-4" fill="#fff"/><circle cx="21" cy="15" r="4" fill="#fff"/></svg>Add Review</div>
  </div>
</header>
<nav class="navbar">
  <div class="wrap"><ul><li>About</li><li>Business</li><li>Developers</li><li>Pricacy &amp; Terms</li><li>Copyright &amp; Trademark</li></ul></div>
</nav>

<main>
  <div class="wrap">
    <div class="filters">
      <div class="filter save"><svg width="14" height="14" viewBox="0 0 14 14"><rect x="1" y="1" width="12" height="12" rx="1" fill="none" stroke="#fff" stroke-width="1.6"/><rect x="4" y="1" width="6" height="4" fill="#fff"/></svg>Save</div>
      <div class="filter" style="width:81px"><svg width="14" height="12" viewBox="0 0 14 12"><rect x="1" y="3" width="12" height="8" fill="#bbb"/><rect x="5" y="1" width="4" height="3" fill="none" stroke="#bbb"/></svg>Career<small>(all)</small></div>
      <div class="filter" style="width:122px"><svg width="14" height="12" viewBox="0 0 14 12"><path d="M1 1h12v8H6l-3 3V9H1z" fill="#bbb"/></svg>Specialization<small>(all)</small></div>
      <div class="filter" style="width:101px"><svg width="14" height="14" viewBox="0 0 14 14"><circle cx="7" cy="5" r="3.5" fill="none" stroke="#bbb" stroke-width="1.6"/><ellipse cx="7" cy="12" rx="5" ry="1.5" fill="#bbb"/></svg>Location<small>(Vancouver)</small></div>
      <div class="filter" style="width:109px"><svg width="14" height="14" viewBox="0 0 14 14"><circle cx="7" cy="7" r="6" fill="#bbb"/><text x="7" y="10.5" font-size="9" text-anchor="middle" fill="#fff" font-family="Open Sans,sans-serif">$</text></svg>Price<small>($600-$3000)</small></div>
      <div class="filter" style="width:106px"><svg width="14" height="14" viewBox="0 0 14 14"><rect x="1" y="2" width="12" height="11" fill="none" stroke="#bbb" stroke-width="1.4"/><line x1="1" y1="5" x2="13" y2="5" stroke="#bbb"/></svg>Start Date<small>(2-6 months)</small></div>
      <div class="filter" style="width:113px"><svg width="16" height="14" viewBox="0 0 16 14"><rect x="1" y="9" width="4" height="4" fill="#bbb"/><rect x="6" y="5" width="4" height="8" fill="#bbb"/><rect x="11" y="1" width="4" height="12" fill="#bbb"/></svg>Level<small>(intermediate)</small></div>
      <div class="filter" style="width:88px"><svg width="14" height="14" viewBox="0 0 14 14"><path d="M7 1l6 3v6l-6 3-6-3V4z M1 4l6 3 6-3 M7 7v6" fill="none" stroke="#bbb" stroke-width="1.2"/></svg>Type<small>(multiple)</small></div>
      <div class="filter" style="width:90px"><svg width="14" height="14" viewBox="0 0 14 14"><circle cx="7" cy="6" r="3.5" fill="#bbb"/><rect x="5.5" y="10" width="3" height="3" fill="#bbb"/></svg>Provider<small>(one)</small></div>
    </div>

    <h1 class="page-title">Competency Planning Tool</h1>
    <p class="lead">Get recommendations for the best courses for you by completing a quick self evaluation</p>
    <h2 class="section-title">Skills self-evaluation</h2>
  </div>

  <section class="group shade">
    <div class="wrap">
      <div class="grid">
        <div class="head-q">Question Group 1</div><div class="head-lvl col-adv">Advanced</div><div class="head-lvl col-mod">Moderate</div><div class="head-lvl col-beg">Beginner</div>
        <div class="q row" style="margin-top:20px">Lorem ipsum dolor sit amet, consectetur adipiscing elit<br>onec semper metus ut mauris?</div><div class="radio on col-adv" style="margin-top:20px"></div><div class="radio col-mod" style="margin-top:20px"></div><div class="radio col-beg" style="margin-top:20px"></div>
        <div class="q row">Lorem ipsum dolor sit amet, consectetur adipiscing elit<br>onec semper metus ut mauris?</div><div class="radio on col-adv"></div><div class="radio col-mod"></div><div class="radio col-beg"></div>
        <div class="q row tall">Lorem ipsum dolor sit amet, consectetur adipiscing elit<br>onec semper metus ut mauris?</div><div class="radio on col-adv"></div><div class="radio col-mod"></div><div class="radio col-beg"></div>
      </div>
    </div>
  </section>

  <section class="group">
    <div class="wrap">
      <div class="grid">
        <div class="head-q">Question Group 1</div><div class="head-lvl col-adv">Advanced</div><div class="head-lvl col-mod">Moderate</div><div class="head-lvl col-beg">Beginner</div>
        <div class="q row" style="margin-top:20px">Lorem ipsum dolor sit amet, consectetur adipiscing elit<br>onec semper metus ut mauris?</div><div class="radio on col-adv" style="margin-top:20px"></div><div class="radio col-mod" style="margin-top:20px"></div><div class="radio col-beg" style="margin-top:20px"></div>
        <div class="q row">Lorem ipsum dolor sit amet, consectetur adipiscing elit<br>onec semper metus ut mauris?</div><div class="radio on col-adv"></div><div class="radio col-mod"></div><div class="radio col-beg"></div>
        <div class="q row tall">Lorem ipsum dolor sit amet, consectetur adipiscing elit<br>onec semper metus ut mauris?</div><div class="radio on col-adv"></div><div class="radio col-mod"></div><div class="radio col-beg"></div>
      </div>
    </div>
  </section>

  <section class="group shade">
    <div class="wrap">
      <div class="grid">
        <div class="head-q">Question Group 1</div><div class="head-lvl col-adv">Advanced</div><div class="head-lvl col-mod">Moderate</div><div class="head-lvl col-beg">Beginner</div>
        <div class="q row" style="margin-top:20px">Lorem ipsum dolor sit amet, consectetur adipiscing elit<br>onec semper metus ut mauris?</div><div class="radio on col-adv" style="margin-top:20px"></div><div class="radio col-mod" style="margin-top:20px"></div><div class="radio col-beg" style="margin-top:20px"></div>
        <div class="q row">Lorem ipsum dolor sit amet, consectetur adipiscing elit<br>onec semper metus ut mauris?</div><div class="radio on col-adv"></div><div class="radio col-mod"></div><div class="radio col-beg"></div>
        <div class="q row tall">Lorem ipsum dolor sit amet, consectetur adipiscing elit<br>onec semper metus ut mauris?</div><div class="radio on col-adv"></div><div class="radio col-mod"></div><div class="radio col-beg"></div>
      </div>
    </div>
  </section>

  <a class="next-btn">Next, see recommendations <svg width="12" height="20" viewBox="0 0 12 20"><path d="M2 2l8 8-8 8" fill="none" stroke="#fff" stroke-width="3"/></svg></a>
</main>
</body>
</html>
```